Veranix - Solution provider in business consulting

Veranix is a swiss based company providing solutions for developing markets. The business covers various fields of business consulting, such as supply chain, product costs, quality management and manufacturing management. The Business operates in a efficient, straight and solution oriented manner.
The final design should communicate these characteristics. Asian people as well as as western people shall identify the qualities of the company at first sight.
The customer needs business cards with a simple view but an recognizable design, printed in high quality. Engraved elements such as the globe or simple words are possible.
Available colors are: (RAL)
102/102/102
51/102/102
153/204/153
255/102/51
Font: Calibri

```html
<!DOCTYPE html>
<html lang="en">
<head>
<meta charset="utf-8">
<title>Veranix – Business Cards</title>
<link href="https://fonts.googleapis.com/css2?family=Carlito:wght@400;700&display=swap" rel="stylesheet">
<style>
  :root {
    --backdrop: #e8e6e3;
    --paper: #ffffff;
    --grey: #666666;
    --text-light: #ffffff;
  }
  * { margin: 0; padding: 0; box-sizing: border-box; }
  html, body {
    width: 1200px; height: 900px; overflow: hidden;
    background: var(--backdrop);
    font-family: "Carlito", Calibri, sans-serif;
  }
  .canvas { position: relative; width: 1200px; height: 900px; }
  .card {
    position: absolute;
    background: var(--paper);
    overflow: hidden;
    box-shadow: 0 6px 18px rgba(0,0,0,0.18);
  }
  .card-front { left: 78px; top: 34px; width: 588px; height: 363px; }
  .card-back  { left: 388px; top: 505px; width: 567px; height: 352px; }
  .card-bands { position: absolute; inset: 0; width: 100%; height: 100%; }
  .band { fill: var(--grey); }

  .holder { position: absolute; left: 30px; top: 50px; color: var(--text-light); }
  .holder-name { font-size: 22px; font-weight: 700; line-height: 1; }
  .holder-role { font-size: 16px; margin-top: 3px; margin-left: 2px; }

  .wordmark {
    position: absolute;
    color: var(--grey);
    font-weight: 400;
    letter-spacing: 1px;
    line-height: 1;
  }
  .card-front .wordmark { left: 28px; top: 196px; font-size: 62px; }
  .card-back .wordmark { left: 34px; top: 74px; font-size: 58px; display: flex; align-items: center; gap: 14px; }
  .wordmark-dot { width: 26px; height: 26px; border-radius: 50%; background: var(--grey); }

  .contact-list {
    position: absolute; right: 36px; top: 250px;
    list-style: none; color: var(--text-light);
    font-size: 16px; text-align: right;
  }
  .contact-list li {
    display: flex; justify-content: flex-end; align-items: center;
    gap: 9px; height: 25px;
  }
  .contact-icon { width: 13px; height: 13px; fill: var(--text-light); }

  .company-address {
    position: absolute; right: 30px; top: 276px;
    color: var(--text-light); font-size: 16px; line-height: 21px; text-align: right;
  }
</style>
</head>
<body>
<main class="canvas">

  <section class="card card-front" aria-label="Business card front">
    <svg class="card-bands" viewBox="0 0 588 363" preserveAspectRatio="none" aria-hidden="true">
      <path class="band" d="M0,0 H588 V30 C440,50 300,170 0,145 Z"/>
      <path class="band" d="M0,363 V345 C160,340 330,240 588,225 V363 Z"/>
    </svg>

    <div class="holder">
      <p class="holder-name">Marco Linder</p>
      <p class="holder-role">CEO</p>
    </div>

    <p class="wordmark">veranix</p>

    <ul class="contact-list">
      <li>+41 79 302 5817
        <svg class="contact-icon" viewBox="0 0 12 12" aria-hidden="true"><path d="M3,0 H9 A1,1 0 0 1 10,1 V11 A1,1 0 0 1 9,12 H3 A1,1 0 0 1 2,11 V1 A1,1 0 0 1 3,0 Z M3.5,1.5 V9.5 H8.5 V1.5 Z M5.5,10 H6.5 V11 H5.5 Z"/></svg>
      </li>
      <li>+41 71 846 3390
        <svg class="contact-icon" viewBox="0 0 12 12" aria-hidden="true"><path d="M2.5,0.5 L4.5,0.5 L5.5,3.5 L4,4.8 C4.8,6.5 5.5,7.2 7.2,8 L8.5,6.5 L11.5,7.5 L11.5,9.5 C11.5,10.8 10.5,11.5 9.5,11.5 C4.5,11 1,7.5 0.5,2.5 C0.5,1.5 1.2,0.5 2.5,0.5 Z"/></svg>
      </li>
      <li>marco.linder@veranix.ch
        <svg class="contact-icon" viewBox="0 0 12 12" aria-hidden="true"><path d="M0,2 H12 V10 H0 Z M1,3 L6,7 L11,3 V9 H1 Z" fill-rule="evenodd"/></svg>
      </li>
      <li>www.veranix.ch
        <svg class="contact-icon" viewBox="0 0 12 12" aria-hidden="true"><circle cx="6" cy="6" r="6"/><path d="M6,1 V11 M1,6 H11 M6,1 C3,4 3,8 6,11 C9,8 9,4 6,1" stroke="#666" stroke-width="0.9" fill="none"/></svg>
      </li>
    </ul>
  </section>

  <section class="card card-back" aria-label="Business card back">
    <svg class="card-bands" viewBox="0 0 567 352" preserveAspectRatio="none" aria-hidden="true">
      <path class="band" d="M0,352 V300 C200,300 380,220 567,215 V352 Z"/>
    </svg>

    <p class="wordmark">veranix<span class="wordmark-dot"></span></p>

    <p class="company-address">Veranix GmbH Feldweg 14<br>9247 Ahrenwil Switzerland</p>
  </section>

</main>
</body>
</html>
```